Social Media App Needs PPT Template

We need a PowerPoint template for a new social media company based in the DC area called "Bold Ledger." We provide an interactive digital platform for executives to share actionable advice. We would like to see designs that use our orange logo color as an accent, but are mainly grey, white, and black. The final design should communicate clean, chic, modern, and professional.

Target Market(s)

Executives

Industry/Entity Type

Information Technology

Font styles to use
Sans Serif

Colors
f78f20
fbe7d2
ffffff
000000
e8e8e8
757575

Requirements
Must have
• My project must have title page and many options for the body of the ppt (graphs, tables, etc). It also needs to be easy to modify. I must have someone who is experienced in creating powerpoint templates.
Nice to have
• It would be nice to have a very modern and clean design that includes the logo on every page, but still leaves a lot of room for the content of the slide
Should not have
• My design project should not look to busy.

```html
<!DOCTYPE html>
<html lang="en">
<head>
<meta charset="utf-8">
<title>Bold Ledger – Team Slide</title>
<link href="https://fonts.googleapis.com/css2?family=Lato:wght@300;400;700&family=Oswald:wght@500&display=swap" rel="stylesheet">
<style>
  :root {
    --stage: #555555;
    --paper: #ffffff;
    --accent: #f18d1f;
    --navy: #232b37;
    --heading: #2b3440;
    --muted: #777777;
    --body: #444444;
    --rule: #555555;
  }
  * { margin: 0; padding: 0; box-sizing: border-box; }
  html, body {
    width: 1200px; height: 960px; overflow: hidden;
    background: var(--stage);
    font-family: "Lato", sans-serif;
  }
  .slide {
    position: absolute; left: 0; top: 30px;
    width: 1200px; height: 900px;
    background: var(--paper);
  }
  .accent-band {
    position: absolute; left: 0; top: 18px;
    width: 100%; height: 14px;
    background: var(--accent);
  }
  .header-bar {
    position: absolute; left: 0; top: 35px;
    width: 100%; height: 116px;
    background: var(--navy);
  }
  .slide-title {
    position: absolute; left: 50px; top: 24px;
    font-family: "Oswald", sans-serif; font-weight: 500;
    font-size: 56px; line-height: 68px; letter-spacing: -1px;
    color: var(--paper); text-transform: uppercase;
  }
  .brand {
    position: absolute; right: 48px; top: 40px;
    display: flex; align-items: center; gap: 12px;
  }
  .brand-dot {
    width: 30px; height: 30px; border-radius: 50%;
    background: var(--accent);
  }
  .brand-name {
    font-family: "Lato", sans-serif; font-weight: 700;
    font-size: 28px; color: var(--paper); line-height: 36px;
  }
  .profile {
    position: absolute; width: 530px; height: 170px;
  }
  .profile-photo {
    position: absolute; left: 0; top: 0;
    width: 149px; height: 168px;
  }
  .profile-text {
    position: absolute; left: 169px; top: 4px; width: 356px;
  }
  .profile-name {
    font-weight: 700; font-size: 27px; line-height: 34px;
    color: var(--heading);
  }
  .profile-role {
    font-weight: 300; font-size: 19px; line-height: 26px;
    color: var(--muted); margin-bottom: 8px;
  }
  .profile-bio {
    font-weight: 400; font-size: 16.5px; line-height: 21.4px;
    color: var(--body); text-align: justify;
  }
  .p-a { left: 53px; top: 242px; }
  .p-c { left: 628px; top: 242px; }
  .p-b { left: 53px; top: 544px; }
  .p-d { left: 628px; top: 544px; }
  .photo-a { background: linear-gradient(160deg, #c9d6de 0%, #a98c78 45%, #2d3238 100%); }
  .photo-c { background: linear-gradient(180deg, #b9b9bb 0%, #c79d84 50%, #3a3a3c 100%); }
  .photo-b { background: linear-gradient(150deg, #c9b37a 0%, #b98a6a 45%, #a9bfd6 100%); }
  .photo-d { background: linear-gradient(160deg, #e4ddd3 0%, #c79b82 50%, #b9c9dc 100%); }
  .footer-rule {
    position: absolute; left: 806px; top: 832px;
    width: 353px; height: 1px; background: var(--rule);
  }
  .footer-text {
    position: absolute; right: 43px; top: 855px;
    font-size: 15.5px; line-height: 20px; color: var(--muted);
  }
</style>
</head>
<body>
  <main class="slide">
    <div class="accent-band"></div>
    <header class="header-bar">
      <h1 class="slide-title">Title Goes Here</h1>
      <div class="brand">
        <span class="brand-dot"></span>
        <span class="brand-name">Bold Ledger</span>
      </div>
    </header>

    <section class="profile p-a">
      <div class="profile-photo photo-a" role="img" aria-label="Portrait photo of Mr A. Smith"></div>
      <div class="profile-text">
        <h2 class="profile-name">Mr A. Smith</h2>
        <p class="profile-role">(President)</p>
        <p class="profile-bio">Lorem ipsum dolor sit amet, consectetuer adipiscing elit, s ed diam nonu mmy nibh euis mod tincidunt ut laoreet do lore magna aliquam erat vol utp at. Ut wisi enim ad min im veniam, quis nostrud exerci ta tion.</p>
      </div>
    </section>

    <section class="profile p-c">
      <div class="profile-photo photo-c" role="img" aria-label="Portrait photo of Mr C. Smith"></div>
      <div class="profile-text">
        <h2 class="profile-name">Mr C. Smith</h2>
        <p class="profile-role">(President)</p>
        <p class="profile-bio">Lorem ipsum dolor sit amet, consectetuer adipiscing elit, s ed diam nonu mmy nibh euis mod tincidunt ut laoreet do lore magna aliquam erat vol utp at. Ut wisi enim ad min im veniam, quis nostrud exerci ta tion.</p>
      </div>
    </section>

    <section class="profile p-b">
      <div class="profile-photo photo-b" role="img" aria-label="Portrait photo of Mr B. Smith"></div>
      <div class="profile-text">
        <h2 class="profile-name">Mr B. Smith</h2>
        <p class="profile-role">(President)</p>
        <p class="profile-bio">Lorem ipsum dolor sit amet, consectetuer adipiscing elit, s ed diam nonu mmy nibh euis mod tincidunt ut laoreet do lore magna aliquam erat vol utp at. Ut wisi enim ad min im veniam, quis nostrud exerci ta tion.</p>
      </div>
    </section>

    <section class="profile p-d">
      <div class="profile-photo photo-d" role="img" aria-label="Portrait photo of Mr D. Smith"></div>
      <div class="profile-text">
        <h2 class="profile-name">Mr D. Smith</h2>
        <p class="profile-role">(President)</p>
        <p class="profile-bio">Lorem ipsum dolor sit amet, consectetuer adipiscing elit, s ed diam nonu mmy nibh euis mod tincidunt ut laoreet do lore magna aliquam erat vol utp at. Ut wisi enim ad min im veniam, quis nostrud exerci ta tion.</p>
      </div>
    </section>

    <div class="footer-rule"></div>
    <p class="footer-text">www.boldledger.com&nbsp; | &nbsp;Page 8</p>
  </main>
</body>
</html>
```